Moravel Aesthetic Doctor

I require an elegant, luxurious looking business card for my aesthetic business. I am a doctor and that will set me aside from competitors. I am planning to provide home and spa based treatments to clients with high expectations. I have attached my logo.

```html
<!DOCTYPE html>
<html lang="en">
<head>
<meta charset="utf-8">
<title>Moravel Aesthetic Doctor — Business Card</title>
<link href="https://fonts.googleapis.com/css2?family=Work+Sans:wght@400;500;600&display=swap" rel="stylesheet">
<style>
  :root {
    --backdrop: #161616;
    --card: #1f1f20;
    --card-edge: #2a2a2b;
    --ink: #f2f2f2;
    --ink-soft: #d6d6d6;
    --ink-muted: #8d8d90;
    --accent: #1aa3e8;
  }
  * { margin: 0; padding: 0; box-sizing: border-box; }
  html, body {
    width: 1200px; height: 900px; overflow: hidden;
    background: var(--backdrop);
    font-family: "Work Sans", Arial, sans-serif;
  }
  .canvas { position: relative; width: 1200px; height: 900px; }
  .card {
    position: absolute; left: 260px; width: 680px; height: 389px;
    background: var(--card);
    border: 1px solid var(--card-edge);
    border-radius: 3px;
  }
  .card--back { top: 48px; }
  .card--front { top: 468px; }

  .brand-dot {
    border-radius: 50%;
    border: 2px solid currentColor;
    flex: none;
  }
  .brand-name {
    font-weight: 400; letter-spacing: 2px;
    line-height: 1.2; text-transform: uppercase;
    white-space: nowrap;
  }
  .brand-name span { display: block; }

  /* back side */
  .back-brand {
    position: absolute; left: 0; right: 0; top: 120px;
    display: flex; align-items: center; justify-content: center; gap: 16px;
    color: var(--ink-muted);
  }
  .back-brand .brand-dot { width: 58px; height: 58px; }
  .back-brand .brand-name { font-size: 22px; }
  .services {
    position: absolute; left: 0; right: 0; top: 260px;
    text-align: center; color: var(--ink);
    font-size: 17px; letter-spacing: 1.6px; line-height: 1.6;
  }
  .services .sep { color: var(--accent); padding: 0 6px; }

  /* front side */
  .front-brand {
    position: absolute; left: 36px; top: 136px;
    display: flex; align-items: center; gap: 12px;
    color: var(--accent);
  }
  .front-brand .brand-dot { width: 48px; height: 48px; }
  .front-brand .brand-name { font-size: 18px; }
  .divider {
    position: absolute; left: 336px; top: 92px;
    width: 1.5px; height: 150px; background: var(--accent);
  }
  .contact {
    position: absolute; left: 362px; top: 92px; color: var(--ink);
  }
  .contact-name {
    color: var(--accent); font-weight: 600; font-size: 20px; letter-spacing: .5px;
    white-space: nowrap;
  }
  .contact-title {
    font-size: 17px; letter-spacing: 1px; line-height: 1.3; margin: 4px 0 8px;
  }
  .contact-line {
    display: flex; align-items: center; gap: 10px;
    font-size: 17px; letter-spacing: 1.2px; line-height: 1.55;
  }
  .contact-line svg { width: 13px; height: 13px; flex: none; }
  .tagline {
    position: absolute; left: 0; right: 0; bottom: 52px;
    text-align: center; color: var(--ink);
    font-size: 17px; letter-spacing: 3px; text-transform: uppercase;
  }
</style>
</head>
<body>
<main class="canvas">

  <section class="card card--back" aria-label="Card back">
    <div class="back-brand">
      <span class="brand-dot"></span>
      <p class="brand-name"><span>Moravel</span><span>Aesthetic Doctor</span></p>
    </div>
    <p class="services">
      Dermal injectables<span class="sep">|</span>Plasma facials<span class="sep">|</span>Microneedling<br>
      Skin boosters<span class="sep">|</span>Excessive sweating
    </p>
  </section>

  <section class="card card--front" aria-label="Card front">
    <div class="front-brand">
      <span class="brand-dot"></span>
      <p class="brand-name"><span>Moravel</span><span>Aesthetic Doctor</span></p>
    </div>
    <span class="divider"></span>
    <div class="contact">
      <p class="contact-name">Dr Elise Varden MRCPCH MD</p>
      <p class="contact-title">Australasian Diploma<br>of Aesthetic Medicine</p>
      <p class="contact-line">
        <svg viewBox="0 0 16 16" fill="none" stroke="var(--accent)" stroke-width="1.6"><path d="M4 1.5l2.5 3-1.6 1.6a9 9 0 0 0 5 5l1.6-1.6 3 2.5-1.5 2.5C7 14 2 9 1.5 3z"/></svg>
        0800 555 014
      </p>
      <p class="contact-line">
        <svg viewBox="0 0 16 16" fill="none" stroke="var(--accent)" stroke-width="1.6"><rect x="1.5" y="3.5" width="13" height="9" rx="1"/><path d="M1.5 4l6.5 5 6.5-5"/></svg>
        elise@moravel.co.nz
      </p>
      <p class="contact-line">
        <svg viewBox="0 0 16 16" fill="none" stroke="var(--accent)" stroke-width="1.4"><circle cx="8" cy="8" r="6.5"/><ellipse cx="8" cy="8" rx="3" ry="6.5"/><path d="M1.5 8h13"/></svg>
        www.moravel.co.nz
      </p>
    </div>
    <p class="tagline">Home and spa based treatments</p>
  </section>

</main>
</body>
</html>
```